Agrarhandel benötigt Homepage
Zielgruppe
Wir sind ein Agrarhandel mit einem Warenumschlagslager im Sinne eines klassischen Einzelhandels und vertreiben Produkte an Landwirte.
Wir vertreiben folgende Hauptproduktgruppen:
Einzelfuttermittel
wie z.B. Sojaexktraktionsschrot. Die einzelnen Produkte könnten z.B. wie die Futtermittel auf folgender Seite dargestellt werden (https://www.kornprobe-beispiel.eu/de/produkt/trelomixan)
Mischfuttermittel
Hier bieten wir unseren Kunden an, individuelles Mischfutter auf Basis unserer Einzelfuttermittel herzustellen.
Weitere Details und weitere Produktbereiche habe ich in einer Powerpoint-Übersicht dargestellt.
Neben diesen Produkten wollen wir uns als Familienunternehmen selbst vorstellen. Zudem betreiben wir in unserer Familie zusätzlich einen Milchviehbetrieb den wir ebenfalls hervorheben möchten, da wir unseren Kunden gegenüber einerseits als Zulieferer aber auch als Kollege auftreten wollen.
Einzelfuttermittel: Hier können wir durch unsere Unabhängigkeit punkten, da wir nicht abhängig von bestimmten Lieferanten sind und dementsprechend unabhängig beraten können. Wir untersuchen im Vergleich zu unseren Wettbewerben die Qualität der Futtermittel bis ins Detail und können daher eine Transparenz bieten, die Konkurrenten in der Regel nicht bieten können. Unser Warenumschlagsplatz mit moderner Technik ermöglicht es uns äußerst kosteneffizient die Waren umschlagen und ausliefern zu können.
Mischfuttermittel: Auf Basis der vorhandenen Einzelfuttermittel stellen wir je nach Kundenwunsch individuelle Mischfutter her. Wir arbeiten mit offenen Deklarationen, sodass unsere Kunden jederzeit nachvollziehen können, ob auch die Einzelfuttermittel verwendet wurden, die sie bestellt haben und keine billigen Ersatzprodukte verwendet wurden.
Zudem sind wir BT und HUPA zertifiziert. Die aktuellen für unser Unternehmen ausgestellten Zertifikate müssen für unsere Kunden als Download zur Verfügung stehen. Statt dem HUPA-Logo bitte das ..
Aufgabenstellung
Wir möchten gerne ein zeitgemäße Homepage, jedoch muss auch berücksichtigt werden, dass unsere Kunden eher konservativ denken.

```html
<!DOCTYPE html>
<html lang="de">
<head>
<meta charset="utf-8">
<title>Albtal Agrarhandel – In der Heimat verwurzelt</title>
<link rel="stylesheet" href="https://fonts.googleapis.com/css2?family=Roboto:wght@400;500;700&family=Roboto+Condensed:wght@700&family=Poppins:wght@500;700&display=swap">
<style>
  :root {
    --yellow: #f2c72e;
    --ink: #1d1d1b;
    --muted: #7a7a74;
    --line: #d8d6cf;
    --cream: #faf7f0;
    --white: #ffffff;
    --forest: #1d2a18;
    --field-green: #6f8f4a;
    --field-dark: #3f5a2c;
    --wheat: #a8865a;
    --wheat-dark: #6e5533;
    --send-green: #7bb342;
  }
  * { box-sizing: border-box; margin: 0; padding: 0; }
  html, body { width: 1200px; height: 800px; overflow: hidden; }
  body { position: relative; background: var(--white); color: var(--ink); font-family: "Roboto", sans-serif; }

  .placeholder { display: block; }

  /* Hero with location card */
  .hero { position: absolute; top: 0; left: 0; right: 0; height: 200px; }
  .hero-photo { position: absolute; inset: 0; background: linear-gradient(160deg, #4e6b35 0%, var(--field-green) 35%, #9a9a7a 55%, #8fa865 75%, var(--field-dark) 100%); }
  .location-card { position: absolute; left: 470px; top: 18px; width: 260px; height: 166px; background: rgba(255,255,255,0.92); box-shadow: 0 6px 20px rgba(0,0,0,0.18); }
  .brand { height: 42px; display: flex; align-items: center; justify-content: center; gap: 8px; font-weight: 700; font-size: 17px; color: var(--ink); }
  .brand-dot { width: 14px; height: 14px; border-radius: 50%; background: var(--yellow); }
  .location-map { position: absolute; left: 12px; right: 12px; top: 42px; bottom: 12px; background: linear-gradient(135deg, #dedede, #c9c9c9); }

  /* Quick action rail */
  .quick-rail { position: absolute; right: 0; top: 270px; display: flex; flex-direction: column; gap: 2px; z-index: 5; }
  .quick-rail a { width: 36px; height: 36px; background: var(--yellow); display: flex; align-items: center; justify-content: center; }
  .quick-rail svg { width: 18px; height: 18px; stroke: var(--white); fill: none; stroke-width: 1.8; stroke-linecap: round; stroke-linejoin: round; }

  /* News */
  .news { position: absolute; top: 200px; left: 0; right: 0; height: 255px; padding-top: 12px; text-align: center; }
  .news-kicker { font-family: "Poppins", sans-serif; font-weight: 500; font-size: 12px; line-height: 16px; }
  .news-title { font-family: "Poppins", sans-serif; font-weight: 700; font-size: 24px; line-height: 28px; }
  .news-grid { display: grid; grid-template-columns: repeat(3, 280px); gap: 24px; justify-content: center; margin-top: 10px; text-align: left; }
  .news-image { height: 100px; }
  .img-garden { background: linear-gradient(135deg, #6f8e45, #b89a6c 60%, #4c6a30); }
  .img-seedling { background: linear-gradient(135deg, #e9e6de, #e5b52a 55%, #5a7a3a); }
  .img-harvest { background: linear-gradient(180deg, #6a9ccc 0%, #a9c7e0 45%, #c49a4a 60%, #a07b38 100%); }
  .news-tag { margin-top: 7px; font-size: 9px; line-height: 11px; font-weight: 500; letter-spacing: 0.5px; color: var(--muted); }
  .news-heading { font-size: 13px; font-weight: 500; line-height: 16px; margin-top: 3px; }
  .news-meta { font-size: 9px; line-height: 12px; color: var(--muted); margin-top: 4px; }

  /* Roots band */
  .roots { position: absolute; top: 455px; left: 0; right: 0; height: 140px; text-align: center; color: var(--white); }
  .roots-photo { position: absolute; inset: 0; background: linear-gradient(115deg, var(--wheat-dark) 0%, var(--wheat) 40%, #b8976a 60%, var(--wheat-dark) 100%); }
  .roots-content { position: relative; padding-top: 16px; }
  .roots-title { font-family: "Roboto Condensed", sans-serif; font-weight: 700; font-size: 32px; line-height: 36px; }
  .roots-lead { font-family: "Roboto Condensed", sans-serif; font-weight: 700; font-size: 14px; line-height: 18px; margin-top: 6px; }
  .btn { display: inline-block; background: var(--yellow); color: var(--white); font-size: 11px; line-height: 14px; font-weight: 500; padding: 6px 22px; margin-top: 10px; text-decoration: none; }

  /* Contact */
  .contact { position: absolute; top: 595px; left: 0; right: 0; height: 130px; background: var(--cream); }
  .contact-intro { position: absolute; left: 150px; top: 10px; width: 420px; }
  .contact-title { font-family: "Roboto Condensed", sans-serif; font-weight: 700; font-size: 24px; line-height: 28px; }
  .contact-text { font-size: 11px; line-height: 14px; margin-top: 2px; }
  .contact-image { position: relative; margin-top: 8px; height: 56px; width: 420px; background: linear-gradient(90deg, #7a5a44, #e8e0d4 40%, #c9b08a 70%, #8a6a50); }
  .contact-image::before { content: ""; position: absolute; left: 120px; right: 0; top: 0; height: 10px; background: var(--ink); }
  .contact-form { position: absolute; left: 640px; top: 8px; width: 400px; height: 114px; background: var(--white); padding: 4px 26px 0; }
  .field { display: flex; align-items: center; gap: 10px; height: 25px; border-bottom: 1px solid var(--line); font-size: 11px; color: var(--muted); }
  .field svg { width: 14px; height: 14px; fill: none; stroke: var(--muted); stroke-width: 1.5; stroke-linecap: round; stroke-linejoin: round; }
  .btn-send { margin-top: 8px; background: var(--send-green); padding: 4px 18px; font-size: 10px; }

  /* Footer */
  .footer { position: absolute; top: 725px; left: 0; right: 0; height: 75px; background: var(--forest); color: var(--white); }
  .footer-claim { position: absolute; left: 150px; top: 9px; width: 270px; font-size: 11px; font-weight: 500; line-height: 14px; }
  .footer-contact { position: absolute; left: 520px; top: 12px; font-size: 10px; line-height: 15px; color: #d6dccd; }
  .footer-image { position: absolute; left: 820px; top: 8px; width: 180px; height: 44px; background: linear-gradient(135deg, #e9ddc2, #c8b088); }
  .footer-nav { position: absolute; left: 150px; bottom: 5px; display: flex; gap: 18px; font-size: 9px; line-height: 11px; color: #c9d0bf; }
  .footer-copy { position: absolute; right: 200px; bottom: 5px; font-size: 9px; line-height: 11px; color: #9aa48f; }
</style>
</head>
<body>

<header class="hero">
  <div class="hero-photo placeholder" role="img" aria-label="Luftaufnahme eines Dorfes zwischen Feldern und Wäldern"></div>
  <div class="location-card">
    <div class="brand"><span class="brand-dot"></span>Albtal Agrarhandel</div>
    <div class="location-map placeholder" role="img" aria-label="Karte mit den Standorten des Agrarhandels"></div>
  </div>
</header>

<nav class="quick-rail" aria-label="Schnellzugriff">
  <a href="#" aria-label="Shop"><svg viewBox="0 0 24 24"><path d="M3 4h3l2 11h11l2-8H7"/><circle cx="10" cy="19" r="1.5"/><circle cx="17" cy="19" r="1.5"/></svg></a>
  <a href="#" aria-label="Zertifikate"><svg viewBox="0 0 24 24"><rect x="4" y="4" width="16" height="16" rx="2"/><path d="M8 14l3-3 5 5"/><circle cx="15" cy="9" r="1.5"/></svg></a>
  <a href="#" aria-label="Termine"><svg viewBox="0 0 24 24"><rect x="3" y="5" width="18" height="15" rx="1"/><path d="M3 9h18"/></svg></a>
</nav>

<section class="news">
  <p class="news-kicker">Oktober</p>
  <h2 class="news-title">Aktuelles</h2>
  <div class="news-grid">
    <article>
      <div class="news-image img-garden placeholder" role="img" aria-label="Gemüseernte im Garten"></div>
      <p class="news-tag">CROP</p>
      <h3 class="news-heading">Environmental Pollution: Everything You Need to Know</h3>
      <p class="news-meta">Okt 2023</p>
    </article>
    <article>
      <div class="news-image img-seedling placeholder" role="img" aria-label="Setzling in Händen mit Handschuhen"></div>
      <p class="news-tag">CROP</p>
      <h3 class="news-heading">The Most Important Facts About Digital Farming</h3>
      <p class="news-meta">Okt 2023</p>
    </article>
    <article>
      <div class="news-image img-harvest placeholder" role="img" aria-label="Mähdrescher im Getreidefeld"></div>
      <p class="news-tag">CROP</p>
      <h3 class="news-heading">Top Five Strategies to Protect Crops from Wild Animals</h3>
      <p class="news-meta">Okt 2023</p>
    </article>
  </div>
</section>

<section class="roots">
  <div class="roots-photo placeholder" role="img" aria-label="Luftaufnahme eines Mähdreschers auf dem Weizenfeld"></div>
  <div class="roots-content">
    <h1 class="roots-title">In der heimat Verwurzelt</h1>
    <p class="roots-lead">Bauen Sie auf den Verlässlichen Partner<br>der Regionalen Landwirtschaft</p>
    <a class="btn" href="#kontakt">Kontakt</a>
  </div>
</section>

<section class="contact" id="kontakt">
  <div class="contact-intro">
    <h2 class="contact-title">Kontakt</h2>
    <p class="contact-text">Bei Fragen oder Anregungen nehmen Sie gerne Kontakt mit uns auf</p>
    <div class="contact-image placeholder" role="img" aria-label="Milchkühe im Stall beim Fressen"></div>
  </div>
  <form class="contact-form">
    <label class="field"><svg viewBox="0 0 24 24"><circle cx="12" cy="8" r="4"/><path d="M4 21c1-4 4-6 8-6s7 2 8 6"/></svg>Name</label>
    <label class="field"><svg viewBox="0 0 24 24"><path d="M5 3h4l2 5-3 2a11 11 0 0 0 6 6l2-3 5 2v4a2 2 0 0 1-2 2A17 17 0 0 1 3 5a2 2 0 0 1 2-2z"/></svg>Phone</label>
    <label class="field"><svg viewBox="0 0 24 24"><rect x="3" y="5" width="18" height="14"/><path d="M3 6l9 7 9-7"/></svg>Email Address</label>
    <a class="btn btn-send" href="#">Senden</a>
  </form>
</section>

<footer class="footer">
  <p class="footer-claim">Sie möchten mehr über Albtal Agrarhandel erfahren? Dann nehmen Sie Kontakt zu uns auf, wir sind gerne für Sie da!</p>
  <p class="footer-contact">Tel. 09100 123 456<br>info@albtal-agrar.de</p>
  <div class="footer-image placeholder" role="img" aria-label="Haufen Futtermittelschrot"></div>
  <nav class="footer-nav"><span>Start</span><span>Aktuelles</span><span>Futtermittel</span><span>Kontakt</span><span>Shop</span><span>Impressum</span></nav>
  <p class="footer-copy">© 2023 Albtal Agrarhandel</p>
</footer>

</body>
</html>
```